Brightmill Data Works

Our company is about IT hardwares and IT solutions. IT hardware such as PC, RAMS, storage and servers. IT solutions such as project management, BA. We are also selling new technology too.

Target Market(s)

Consumer, Small to Medium Business, Corporate

Requirements
Must have
• The business card must have the following:
• Name:
• Title:
• Contact Number:
• Email address:
• Website:
• Color: Must match the logo color upgrade

```html
<!DOCTYPE html>
<html lang="en">
<head>
<meta charset="utf-8">
<title>Brightmill Data Works – Business Card</title>
<link rel="stylesheet" href="https://fonts.googleapis.com/css2?family=Lato:wght@400;700;900&display=swap">
<style>
  :root {
    --backdrop: #2b2b2b;
    --card-dark: #222222;
    --card-light: #ffffff;
    --accent: #de9a3c;
    --ink-dark: #3a3a3a;
    --ink-light: #f4f4f4;
  }
  * { box-sizing: border-box; margin: 0; padding: 0; }
  html, body {
    width: 1200px; height: 900px; overflow: hidden;
    background: var(--backdrop);
    font-family: "Lato", sans-serif;
  }
  .canvas { position: relative; width: 1200px; height: 900px; }

  .card {
    position: absolute; left: 267px;
    width: 665px; height: 380px;
    background: var(--card-dark);
    overflow: hidden;
    box-shadow: 0 14px 30px rgba(0,0,0,.45);
  }
  .card--back { top: 50px; }
  .card--front { top: 470px; }

  /* Back side */
  .brand {
    display: flex; align-items: center; gap: 14px;
    font-weight: 900; text-transform: uppercase;
    letter-spacing: 1px; white-space: nowrap;
  }
  .brand__dot {
    width: 30px; height: 30px; border-radius: 50%;
    background: var(--accent); flex: none;
  }
  .card--back .brand {
    position: absolute; left: 50%; top: 150px;
    transform: translateX(-50%);
    font-size: 34px; color: var(--ink-light);
  }
  .card--back .website {
    position: absolute; left: 0; right: 0; top: 268px;
    text-align: center; color: var(--ink-light);
    font-size: 15px; letter-spacing: .5px;
  }

  /* Front side */
  .swoosh { position: absolute; inset: 0; width: 665px; height: 380px; }
  .card--front .brand {
    position: absolute; left: 395px; top: 150px;
    font-size: 22px; color: var(--ink-dark); gap: 10px;
    flex-direction: column; align-items: flex-start;
  }
  .card--front .brand__dot { width: 26px; height: 26px; }
  .card--front .brand__name { line-height: 1.1; }

  .contact { position: absolute; left: 62px; top: 112px; color: var(--ink-light); }
  .contact__name { color: var(--accent); font-size: 25px; font-weight: 700; }
  .contact__title { font-size: 16px; margin-top: 2px; }
  .contact__address { font-size: 16px; margin-top: 20px; line-height: 1.3; }
  .contact__list { list-style: none; margin-top: 20px; font-size: 16px; }
  .contact__list li { display: flex; align-items: center; gap: 12px; height: 22px; }
  .contact__list svg { width: 14px; height: 14px; fill: var(--accent); flex: none; }
</style>
</head>
<body>
<main class="canvas">

  <section class="card card--back" aria-label="Card back">
    <div class="brand"><span class="brand__dot"></span><span>Brightmill Data Works</span></div>
    <p class="website">www.brightmilldata.com</p>
  </section>

  <section class="card card--front" aria-label="Card front">
    <svg class="swoosh" viewBox="0 0 665 380" aria-hidden="true">
      <path d="M282,0 C250,170 360,368 520,380 L665,380 L665,0 Z" fill="var(--accent)"/>
      <path d="M312,0 C286,165 375,360 540,380 L665,380 L665,0 Z" fill="var(--card-dark)"/>
      <path d="M330,0 C306,160 392,352 565,380 L665,380 L665,0 Z" fill="var(--card-light)"/>
    </svg>

    <div class="brand">
      <span class="brand__dot"></span>
      <span class="brand__name">Brightmill<br>Data Works</span>
    </div>

    <div class="contact">
      <p class="contact__name">Dana Whitlock</p>
      <p class="contact__title">Manager</p>
      <p class="contact__address">418 Alder Court<br>Fairview, TX 75069</p>
      <ul class="contact__list">
        <li>
          <svg viewBox="0 0 16 16"><path d="M3 1l3 0 1.5 4-2 1.3a9 9 0 0 0 4.2 4.2L11 8.5l4 1.5v3a2 2 0 0 1-2 2A13 13 0 0 1 1 3a2 2 0 0 1 2-2z"/></svg>
          <span>555 014 2280</span>
        </li>
        <li>
          <svg viewBox="0 0 16 16"><path d="M4 1h8v4H4zM1 6h14v6h-3v3H4v-3H1zM5 10v4h6v-4z"/></svg>
          <span>555 014 2281</span>
        </li>
        <li>
          <svg viewBox="0 0 16 16"><path d="M1 3h14v10H1zM2.5 4.5v.5L8 9l5.5-4v-.5z"/></svg>
          <span>hello@brightmilldata.com</span>
        </li>
        <li>
          <svg viewBox="0 0 16 16"><path d="M8 1a7 7 0 1 0 0 14A7 7 0 0 0 8 1zm-.8 1.7C6.3 3.8 5.8 5.3 5.7 7H2.6a5.5 5.5 0 0 1 4.6-4.3zm1.6 0A5.5 5.5 0 0 1 13.4 7h-3.1c-.1-1.7-.6-3.2-1.5-4.3zM7.2 7V3.5C6.7 4.4 6.3 5.6 6.2 7zm1.6 0h1c-.1-1.4-.5-2.6-1-3.5zM2.6 9h3.1c.1 1.7.6 3.2 1.5 4.3A5.5 5.5 0 0 1 2.6 9zm3.6 0h1v3.5C6.7 11.6 6.3 10.4 6.2 9zm2.6 0h1c-.1 1.4-.5 2.6-1 3.5zm1.5 0h3.1a5.5 5.5 0 0 1-4.6 4.3c.9-1.1 1.4-2.6 1.5-4.3z"/></svg>
          <span>www.brightmilldata.com</span>
        </li>
      </ul>
    </div>
  </section>

</main>
</body>
</html>
```